Harrow Hide Revival Product Label

We need a design for a label to be used on bottles of leather cleaner and conditioner products that will be used in curated kits. We would like it to incorporate our business logo as well as have an area that we can fill in later with the appropriate product name as needed. We would like to see designs that use shades of brown, but we are open to other colors often seen in leather. I am including the Harrow Hide business Logo below, however again we would prefer to have the label in various shades of browns, rather than the red and grey, more like the mock-up that I am also attaching.

*** I am attaching examples of the types of bottles that will be used. They vary in size from 8 oz to 16 oz. if you are designing a label for a spray bottle they are from 16-32 oz. ***

```html
<!DOCTYPE html>
<html lang="en">
<head>
<meta charset="UTF-8">
<title>Harrow Hide Revival – Leather Cleaner / Conditioner Label</title>
<link rel="stylesheet" href="https://fonts.googleapis.com/css2?family=Montserrat:wght@500;600;700;800&display=swap">
<style>
  :root {
    --page-bg: #ecebe8;
    --leather-light: #b06a22;
    --leather-mid: #8a4a1a;
    --leather-dark: #5c2e12;
    --leather-deep: #3f1e0b;
    --cream: #fbf3e6;
    --gold: #f0a43a;
    --gold-line: #e3b35a;
  }
  * { margin: 0; padding: 0; box-sizing: border-box; }
  html, body { width: 1200px; height: 1200px; overflow: hidden; }
  body {
    background: var(--page-bg);
    font-family: "Montserrat", Arial, sans-serif;
    position: relative;
  }
  .label {
    position: absolute;
    left: 320px;
    top: 130px;
    width: 560px;
    height: 940px;
    border-radius: 44px;
    overflow: hidden;
    background: var(--leather-dark);
  }
  .label-leather {
    position: absolute;
    inset: 0;
    width: 100%;
    height: 100%;
  }
  .brand {
    position: absolute;
    top: 62px;
    left: 0;
    width: 100%;
    text-align: center;
    color: var(--cream);
  }
  .brand-dot {
    width: 118px;
    height: 118px;
    border-radius: 50%;
    background: var(--cream);
    margin: 0 auto 16px;
  }
  .brand-name {
    font-weight: 700;
    font-size: 38px;
    letter-spacing: 1px;
    text-transform: uppercase;
  }
  .brand-sub {
    font-weight: 600;
    font-size: 12px;
    letter-spacing: 2.5px;
    text-transform: uppercase;
    margin-top: 6px;
  }
  .product {
    position: absolute;
    left: 62px;
    top: 366px;
  }
  .product-name {
    font-weight: 800;
    font-size: 84px;
    line-height: 1;
    color: var(--cream);
    letter-spacing: 1px;
  }
  .product-type {
    display: inline-block;
    margin-top: 14px;
    font-weight: 700;
    font-size: 27px;
    letter-spacing: 0.5px;
    color: var(--gold);
    background: rgba(40, 18, 6, 0.35);
    padding: 2px 6px;
  }
  .benefits {
    position: absolute;
    left: 62px;
    top: 560px;
    padding-left: 12px;
    border-left: 2px solid var(--gold-line);
    list-style: none;
    color: var(--cream);
    font-weight: 600;
    font-size: 22px;
    line-height: 1.45;
  }
  .hide-icon {
    display: block;
    margin-top: 12px;
    width: 34px;
    height: 38px;
  }
  .volume {
    position: absolute;
    left: 0;
    width: 100%;
    bottom: 86px;
    text-align: center;
    color: var(--cream);
    font-weight: 700;
    font-size: 30px;
  }
</style>
</head>
<body>
  <section class="label">
    <svg class="label-leather" viewBox="0 0 560 940" preserveAspectRatio="none" role="img" aria-label="Brown grained leather texture in two tones">
      <defs>
        <linearGradient id="leatherDarkTone" x1="0" y1="0" x2="1" y2="1">
          <stop offset="0" stop-color="#6a3514"/>
          <stop offset="1" stop-color="#3f1e0b"/>
        </linearGradient>
        <linearGradient id="leatherLightTone" x1="0" y1="0" x2="1" y2="1">
          <stop offset="0" stop-color="#9a5a1e"/>
          <stop offset="0.5" stop-color="#b7722a"/>
          <stop offset="1" stop-color="#8a4a1a"/>
        </linearGradient>
      </defs>
      <rect width="560" height="940" fill="url(#leatherDarkTone)"/>
      <path d="M0 0 H560 V250 C470 330 300 300 230 420 C170 520 250 640 120 760 C80 800 30 820 0 830 Z" fill="url(#leatherLightTone)"/>
      <path d="M0 0 H250 C180 90 60 120 0 190 Z" fill="#7a3e16" opacity="0.55"/>
    </svg>

    <header class="brand">
      <div class="brand-dot"></div>
      <div class="brand-name">Harrow Hide</div>
      <div class="brand-sub">Harrow Hide Revival</div>
    </header>

    <div class="product">
      <h1 class="product-name">LEATHER</h1>
      <p class="product-type">CLEANER / CONDITIONER</p>
    </div>

    <ul class="benefits">
      <li>Protects against drying</li>
      <li>Replenishes</li>
      <li>Cleans</li>
      <li>
        <svg class="hide-icon" viewBox="0 0 34 38" aria-hidden="true">
          <path d="M10 2 C13 5 21 5 24 2 C26 6 30 7 32 8 C29 14 29 24 32 30 C27 31 25 34 24 36 C20 33 14 33 10 36 C9 34 7 31 2 30 C5 24 5 14 2 8 C4 7 8 6 10 2 Z" fill="none" stroke="#fbf3e6" stroke-width="2" stroke-linejoin="round"/>
        </svg>
      </li>
    </ul>

    <p class="volume">24 Fl oz.</p>
  </section>
</body>
</html>
```